Web design for business website

I need a web design for a business website for one of our clients who is specialized in alarm management software. I would like you to design 3 web pages, one for each of the 3 pages. You need to process the corporate identity of our client to the web design. This means the colors of the logo (red and black) should definitely show up on all of the 3 pages. Find the logo file for the logo of our customer. To increase readability I suggest you use a white/light background. All suggestions are welcome.

Please kindly download atttached Webdesign.zip and read the project brief first. The project brief refers to all other files of the zip file. Your design must have exactly the same structure as the wireframes.
Updates

Target Market(s)

B2B, Alarm management

Industry/Entity Type

Business

Number of Pages Required

3 page

Requirements
Must have
• The web design must have exactly the same structure as the wireframes and needs to contain the colors of the company logo.

```html
<!DOCTYPE html>
<html lang="en">
<head>
<meta charset="utf-8">
<title>Logirex – Real-time reasoning solutions</title>
<link href="https://fonts.googleapis.com/css2?family=Open+Sans:wght@300;400;600;700&display=swap" rel="stylesheet">
<style>
:root{
  --red:#e8432a;
  --navy:#1f2536;
  --ink:#2b2b2b;
  --muted:#6d6d6d;
  --topbar:#14161d;
  --footer:#1b1b1b;
  --footer-text:#8a8a8a;
  --white:#ffffff;
}
*{box-sizing:border-box;margin:0;padding:0}
html,body{width:690px;height:1200px;overflow:hidden}
body{font-family:"Open Sans",Arial,sans-serif;color:var(--ink);background:var(--white);position:relative}
.topbar{height:23px;background:var(--topbar);color:#bbb;font-size:9px;display:flex;align-items:center;padding:0 62px;gap:16px}
.topbar span{display:flex;align-items:center;gap:5px}
.header{height:46px;display:flex;align-items:center;justify-content:space-between;padding:0 62px}
.brand{display:flex;flex-direction:column;justify-content:center}
.brand-name{font-size:20px;font-weight:600;color:var(--ink);line-height:1.1}
.brand-tag{font-size:7.5px;font-weight:400;color:var(--muted)}
.header-actions{display:flex;gap:5px}
.header-actions span{width:32px;height:22px;background:var(--red);border-radius:2px;display:flex;align-items:center;justify-content:center}
.nav{height:23px;background:var(--navy);display:flex;padding:0 62px}
.nav a{color:#d7d9df;font-size:8.5px;font-weight:600;text-decoration:none;padding:0 13px;display:flex;align-items:center;letter-spacing:.4px}
.nav a.active{background:var(--red);color:var(--white)}
.hero{position:relative;height:253px}
.hero-photo{position:absolute;inset:0;background:linear-gradient(160deg,#9aa7b4 0%,#5d6a78 40%,#2f3a47 75%,#52606e 100%)}
.hero-card{position:absolute;left:176px;top:42px;width:338px;background:rgba(255,255,255,.88);text-align:center;padding:14px 14px 18px}
.hero-card p{font-size:7.5px;line-height:1.45;color:var(--muted);margin-bottom:10px}
.eyebrow{font-size:10px;font-weight:700;letter-spacing:1px;color:var(--ink)}
.hero-title{font-size:16px;font-weight:400;margin:4px 0 2px;color:var(--ink);white-space:nowrap}
.hero-title b,.section-title b{color:var(--red);font-weight:400}
.btn{display:inline-block;background:var(--red);color:var(--white);font-size:8px;font-weight:700;padding:7px 16px;margin-top:10px;letter-spacing:.5px}
.arrow{position:absolute;top:110px;width:22px;height:30px;background:var(--red);display:flex;align-items:center;justify-content:center}
.arrow.prev{left:0}.arrow.next{right:0}
.welcome{position:relative;height:310px;text-align:center;padding:56px 110px 0}
.welcome-photo{position:absolute;inset:0;background:linear-gradient(180deg,#eef1f4 0%,#dfe4ea 45%,#c9d0d8 100%);opacity:.9}
.welcome>*:not(.welcome-photo){position:relative}
.section-title{font-size:22px;font-weight:400;margin:4px 0 20px}
.welcome p{font-size:8px;line-height:1.55;color:#444;margin-bottom:12px}
.clients{height:207px;text-align:center;padding-top:34px}
.clients h2{font-size:24px;font-weight:400;letter-spacing:.5px;margin-top:2px}
.clients h2 b{color:var(--red);font-weight:400}
.client-row{display:flex;justify-content:space-between;align-items:center;padding:0 70px;margin-top:36px}
.client-row span{font-size:12px;font-weight:700;color:#3d4a6b}
.connect{position:relative;height:104px;display:flex;padding:22px 62px 0;gap:50px}
.connect-photo{position:absolute;inset:0;background:linear-gradient(135deg,#3a434e 0%,#262c33 60%,#323a44 100%)}
.connect>*:not(.connect-photo){position:relative}
.connect h3{font-size:16px;font-weight:400;color:var(--white);letter-spacing:.5px}
.connect h3 b{color:var(--red);font-weight:400}
.socials{display:flex;gap:5px;margin-top:9px}
.socials span{width:20px;height:20px;background:#5b6675}
.subscribe-form{display:flex;margin-top:9px}
.subscribe-form .field{width:300px;height:22px;background:var(--white);font-size:7.5px;color:#999;padding:6px 8px}
.subscribe-form .submit{height:22px;background:var(--navy);color:var(--white);font-size:8px;font-weight:700;padding:6px 14px}
.footer{height:209px;background:var(--footer);display:flex;padding:26px 62px 0}
.footer-col{flex:1}
.footer-col h4{font-size:8.5px;color:var(--white);font-weight:700;letter-spacing:.5px;margin-bottom:9px}
.footer-col li{list-style:none;font-size:7.5px;color:var(--footer-text);line-height:1.75}
.footer-col li.hot{color:var(--red)}
.footer-col li.contact{display:flex;align-items:center;gap:5px}
.copyright{height:25px;background:#111;color:#666;font-size:7.5px;display:flex;align-items:center;justify-content:center}
.copyright b{color:var(--red);font-weight:600;margin:0 3px}
</style>
</head>
<body>
<div class="topbar">
  <span><svg width="8" height="8" viewBox="0 0 10 10"><path d="M2 1l2 2-1 1.5a6 6 0 0 0 2.5 2.5L7 6l2 2-1.5 1.5C4 9 1 6 .5 2z" fill="#bbb"/></svg>+31 (0)00 123 4567</span>
  <span><svg width="9" height="7" viewBox="0 0 10 8"><rect x=".5" y=".5" width="9" height="7" fill="none" stroke="#bbb"/><path d="M.5 .5L5 4.5 9.5 .5" fill="none" stroke="#bbb"/></svg>info@logirex.example</span>
</div>

<header class="header">
  <div class="brand">
    <span class="brand-name">Logirex</span>
    <span class="brand-tag">Real-time reasoning solutions</span>
  </div>
  <div class="header-actions">
    <span><svg width="10" height="10" viewBox="0 0 10 10"><path d="M2 1l2 2-1 1.5a6 6 0 0 0 2.5 2.5L7 6l2 2-1.5 1.5C4 9 1 6 .5 2z" fill="#fff"/></svg></span>
    <span><svg width="10" height="10" viewBox="0 0 10 10"><path d="M5 .5a3.3 3.3 0 0 1 3.3 3.3C8.3 6.3 5 9.5 5 9.5S1.7 6.3 1.7 3.8A3.3 3.3 0 0 1 5 .5z" fill="#fff"/><circle cx="5" cy="3.8" r="1.2" fill="#e8432a"/></svg></span>
    <span><svg width="11" height="8" viewBox="0 0 10 8"><rect x=".5" y=".5" width="9" height="7" fill="none" stroke="#fff"/><path d="M.5 .5L5 4.5 9.5 .5" fill="none" stroke="#fff"/></svg></span>
  </div>
</header>

<nav class="nav">
  <a class="active">HOME</a><a>INDUSTRY</a><a>TELECOM</a><a>POWER</a><a>UTILITIES</a><a>MMMA</a><a>STORE</a>
</nav>

<section class="hero">
  <div class="hero-photo" role="img" aria-label="Industrial plant with pipes and towers at dusk"></div>
  <div class="hero-card">
    <p>We help operators turn floods of alarms into clear decisions. Our software filters, ranks and explains events so teams act fast and keep plants safe every day.</p>
    <div class="eyebrow">HELLO WE ARE</div>
    <h1 class="hero-title"><b>LOGIREX</b> Real-time reasoning solutions</h1>
    <span class="btn">READ MORE</span>
  </div>
  <span class="arrow prev"><svg width="8" height="12" viewBox="0 0 8 12"><path d="M6 1L1 6l5 5" fill="none" stroke="#fff" stroke-width="2"/></svg></span>
  <span class="arrow next"><svg width="8" height="12" viewBox="0 0 8 12"><path d="M2 1l5 5-5 5" fill="none" stroke="#fff" stroke-width="2"/></svg></span>
</section>

<section class="welcome">
  <div class="welcome-photo" role="img" aria-label="Faded view of an industrial control facility"></div>
  <div class="eyebrow">WELCOME TO</div>
  <h2 class="section-title"><b>LOGIREX</b> Real-time reasoning solutions</h2>
  <p>Logirex has been a specialist in alarm management for many years. Our technology gives operators a real-time view of what is happening, filters noise from the control room and points straight to the root cause of every event, so the right person can respond in time.</p>
  <p>Built on proven reasoning methods, our tools combine expert knowledge with live process data. The result is a calm control room, fewer trips and a clear record of every decision made on site.</p>
  <span class="btn">LEARN MORE</span>
</section>

<section class="clients">
  <div class="eyebrow">OUR CLIENTS</div>
  <h2>THAT <b>TRUST US</b></h2>
  <div class="client-row">
    <span>Aridon</span><span>Brookvale</span><span>Tessa</span><span>Norvik</span><span>Halden</span><span>Solvane</span><span>Marlo</span>
  </div>
</section>

<section class="connect">
  <div class="connect-photo" role="img" aria-label="Dark industrial background"></div>
  <div>
    <h3>FOLLOW <b>US ON</b></h3>
    <div class="socials"><span></span><span></span><span></span><span></span><span></span></div>
  </div>
  <div>
    <h3>SUBSCRIBE <b>NOW</b></h3>
    <div class="subscribe-form"><span class="field">Enter your email address</span><span class="submit">SUBSCRIBE</span></div>
  </div>
</section>

<footer class="footer">
  <div class="footer-col"><h4>SOLUTIONS</h4><ul><li class="hot">Alarm Event Reporting</li><li>Alarm Rationalization</li><li>Root Cause Analysis</li><li>Training</li></ul></div>
  <div class="footer-col"><h4>INDUSTRIES</h4><ul><li>Industry</li><li>Telecom</li><li>Power</li><li>Utilities</li><li>MMMA</li></ul></div>
  <div class="footer-col"><h4>ABOUT US</h4><ul><li>Company</li><li>Partners</li><li>Careers</li><li>Customers</li></ul></div>
  <div class="footer-col"><h4>NEWS</h4><ul><li>Product News</li><li>Press Releases</li><li>Events</li><li>Newsletters</li></ul></div>
  <div class="footer-col"><h4>CONTACT US</h4><ul>
    <li class="contact"><svg width="7" height="7" viewBox="0 0 10 10"><path d="M2 1l2 2-1 1.5a6 6 0 0 0 2.5 2.5L7 6l2 2-1.5 1.5C4 9 1 6 .5 2z" fill="#8a8a8a"/></svg>+31 (0)00 123 4567</li>
    <li class="contact"><svg width="8" height="6" viewBox="0 0 10 8"><rect x=".5" y=".5" width="9" height="7" fill="none" stroke="#8a8a8a"/></svg>info@logirex.example</li>
    <li class="contact"><svg width="7" height="8" viewBox="0 0 10 10"><path d="M5 .5a3.3 3.3 0 0 1 3.3 3.3C8.3 6.3 5 9.5 5 9.5S1.7 6.3 1.7 3.8A3.3 3.3 0 0 1 5 .5z" fill="#8a8a8a"/></svg>1 Sample Street, Delft</li>
  </ul></div>
</footer>
<div class="copyright">Copyright © 2024 <b>LOGIREX</b> All rights reserved</div>
</body>
</html>
```